Dynamic Business Card for Sports Supplements Company

Hi! I'm looking for an awesome business card to match my existing sports supplement company. I have uploaded my current company logo and screenshot of the front page of my website.

I would like to have something dynamic and interesting and utilize the colors in the website - the reds and purples

The business card should be double sided and focus on a unique eye-catching design on the back and include all the relevant company info.

Most importantly, it should say somewhere: "Sign up on our website for a coupon code."

Target Market(s)

Mostly for women gym goers but it shouldn't be too feminine. It should be in keeping with the website design. It should flow and clearly be connected to it

Industry/Entity Type

Business

Contact Information for Business Card

Lorraine K. Vestal
CEO
LVestal@Quorvanexco.com
www.quorvanexco.com
555.417.3820
P.O. Box 47315
Larkmoor, Westvale 00000

Sign up on our website for a coupon code

Font styles to use
Serif
Sans Serif
Other font styles liked:
• Novecento font family and "Quorvanex" is in AR Destine font

Requirements
Must have
• One side should be a bold Quorvanex logo design. Even just the symbol itself may be o.k. (see attached file)

```html
<!DOCTYPE html>
<html lang="en">
<head>
<meta charset="utf-8">
<title>Quorvanex Business Card</title>
<link rel="stylesheet" href="https://fonts.googleapis.com/css2?family=Exo+2:wght@400;700&family=Ubuntu:wght@400;500&display=swap">
<style>
  :root {
    --page: #e9e6e2;
    --card-top: #1e1e20;
    --card-bottom: #111113;
    --red: #e0262b;
    --white: #f4f4f4;
    --grey: #c9c9cc;
  }
  * { margin: 0; padding: 0; box-sizing: border-box; }
  html, body {
    width: 1200px; height: 1200px; overflow: hidden;
    background: var(--page);
  }
  .sheet {
    width: 1200px; height: 1200px;
    display: flex; flex-direction: column; align-items: center; justify-content: center;
    gap: 60px;
  }
  .card {
    position: relative;
    width: 900px; height: 514px;
    background: linear-gradient(160deg, var(--card-top), var(--card-bottom));
    box-shadow: 0 10px 28px rgba(0,0,0,.25);
    overflow: hidden;
  }
  /* Brand side */
  .card--brand {
    display: flex; flex-direction: column; align-items: center; justify-content: center;
    text-align: center;
  }
  .brand-name {
    font-family: "Exo 2", sans-serif; font-weight: 700;
    font-size: 72px; letter-spacing: 4px; text-transform: uppercase;
    color: var(--white); line-height: 1;
  }
  .brand-tagline {
    font-family: "Ubuntu", sans-serif; font-size: 17px; letter-spacing: 5px;
    text-transform: uppercase; color: var(--grey); margin-top: 8px;
  }
  .signup {
    font-family: "Ubuntu", sans-serif; font-size: 22px; color: var(--white);
    margin-top: 26px;
  }
  .signup-accent { color: var(--red); }
  /* Contact side */
  .contact { position: absolute; left: 70px; top: 72px; }
  .person-name {
    font-family: "Exo 2", sans-serif; font-weight: 400; font-size: 36px;
    letter-spacing: 3px; text-transform: uppercase; color: var(--red); line-height: 1;
  }
  .person-role {
    font-family: "Ubuntu", sans-serif; font-size: 22px; color: var(--white); margin-top: 8px;
  }
  .contact-list { list-style: none; margin-top: 34px; }
  .contact-item {
    display: flex; align-items: center; gap: 14px;
    font-family: "Ubuntu", sans-serif; font-size: 21px; color: var(--white);
    line-height: 1; margin-bottom: 13px;
  }
  .contact-icon { width: 18px; height: 18px; flex: none; }
  .address {
    font-family: "Ubuntu", sans-serif; font-size: 21px; color: var(--white);
    line-height: 1.45; margin-top: 22px; font-style: normal;
  }
  .brand-ring {
    position: absolute; right: 70px; top: 190px;
    width: 280px; height: 280px; border-radius: 50%;
    border: 9px solid var(--red);
    display: flex; align-items: center; justify-content: center;
  }
  .brand-ring-name {
    font-family: "Exo 2", sans-serif; font-weight: 700; font-size: 31px;
    letter-spacing: 2px; text-transform: uppercase; color: var(--white);
  }
</style>
</head>
<body>
<main class="sheet">
  <section class="card card--brand">
    <div class="brand-name">Quorvanex</div>
    <div class="brand-tagline">Your Performance Partner</div>
    <p class="signup"><span class="signup-accent">Sign up</span> on our website for a coupon code</p>
  </section>

  <section class="card card--contact">
    <div class="contact">
      <h1 class="person-name">Lorraine K. Vestal</h1>
      <p class="person-role">CEO</p>
      <ul class="contact-list">
        <li class="contact-item">
          <svg class="contact-icon" viewBox="0 0 24 24" aria-hidden="true"><path fill="#e0262b" d="M6.6 10.8a15.1 15.1 0 0 0 6.6 6.6l2.2-2.2a1 1 0 0 1 1-.25 11.4 11.4 0 0 0 3.6.57 1 1 0 0 1 1 1V20a1 1 0 0 1-1 1A17 17 0 0 1 3 4a1 1 0 0 1 1-1h3.5a1 1 0 0 1 1 1c0 1.25.2 2.45.57 3.6a1 1 0 0 1-.25 1z"/></svg>
          555.417.3820
        </li>
        <li class="contact-item">
          <svg class="contact-icon" viewBox="0 0 24 24" aria-hidden="true"><rect x="2" y="5" width="20" height="14" rx="2" fill="#e0262b"/><path d="M3 6l9 7 9-7" fill="none" stroke="#151517" stroke-width="2"/></svg>
          LVestal@Quorvanexco.com
        </li>
        <li class="contact-item">
          <svg class="contact-icon" viewBox="0 0 24 24" aria-hidden="true"><circle cx="12" cy="12" r="10" fill="#e0262b"/><path d="M2 12h20M12 2c3 3 3 17 0 20M12 2c-3 3-3 17 0 20" fill="none" stroke="#151517" stroke-width="1.6"/></svg>
          www.quorvanexco.com
        </li>
      </ul>
      <address class="address">P.O. Box 47315<br>Larkmoor, Westvale 00000</address>
    </div>
    <div class="brand-ring"><span class="brand-ring-name">Quorvanex</span></div>
  </section>
</main>
</body>
</html>
```